Beacon Advisory Website

I currently have a website www.beaconadvisoryinc.com. We are a IT Consulting Company. Our website will pretty much tell out our services. I am looking to enhance my website and make it look more professional. Looking for very classy and Contemporary look and design for my website.

It Company

```html
<!DOCTYPE html>
<html lang="en">
<head>
<meta charset="utf-8">
<title>Beacon Advisory</title>
<link rel="stylesheet" href="https://fonts.googleapis.com/css2?family=Raleway:ital,wght@0,400;0,500;0,600;0,700;1,400&display=swap">
<style>
:root{
  --blue:#0a9ad8;
  --blue-dark:#0b4f8a;
  --navy:#1a5ea6;
  --navy-deep:#124a86;
  --ink:#222;
  --muted:#555;
  --pale:#e8ecf0;
  --white:#fff;
}
*{margin:0;padding:0;box-sizing:border-box}
html,body{width:672px;height:1200px;overflow:hidden;background:var(--white)}
body{font-family:"Raleway",sans-serif;color:var(--ink);position:relative}
.abs{position:absolute}

/* header */
.header{top:0;left:0;width:672px;height:50px;border-top:2px solid var(--blue);background:linear-gradient(#fafbfc,#eceff2)}
.brand{left:60px;top:13px;display:flex;align-items:center;gap:6px}
.brand-square{width:20px;height:20px;background:var(--blue-dark)}
.brand-name{font-weight:700;font-size:14px;color:var(--blue-dark)}
.contact-chip{top:14px;display:flex;gap:7px;align-items:center}
.chip-dot{width:19px;height:19px;border-radius:50%;background:var(--blue-dark)}
.chip-label{font-size:6.5px;font-weight:700;color:var(--blue-dark);letter-spacing:.3px}
.chip-value{font-size:8px;color:#444;margin-top:1px}

/* nav */
.nav{top:50px;left:0;width:672px;height:24px;background:linear-gradient(#1a8ed0,#0c6fb3);display:flex;padding-left:60px}
.nav a{color:var(--white);font-size:7.5px;font-weight:700;text-decoration:none;line-height:24px;text-align:center;border-right:1px solid rgba(0,0,0,.12)}
.nav a.active{background:#1fa6e6}

/* hero */
.hero{top:74px;left:0;width:672px;height:228px;background:linear-gradient(90deg,#eef3f8 0%,#dfe9f1 45%,#6b7c8d 70%,#2f3d4d 100%)}
.hero-title{left:60px;top:73px;width:290px;font-size:13.5px;font-weight:700;line-height:18px;color:var(--blue-dark)}
.btn{left:60px;top:139px;width:69px;height:23px;background:var(--blue);color:var(--white);font-size:6.5px;font-weight:700;line-height:23px;text-align:center}

/* welcome */
.welcome{top:302px;left:0;width:672px;height:108px;background:linear-gradient(90deg,#18a3df,#0b8fd0);text-align:center;color:var(--white)}
.welcome h1{font-weight:400;font-size:17px;margin-top:10px}
.welcome .rule{width:150px;height:1px;background:rgba(255,255,255,.7);margin:6px auto 0}
.welcome p{font-size:7px;line-height:12.5px;width:560px;margin:10px auto 0;opacity:.92}
.plus{left:324px;top:396px;width:24px;height:14px;background:#333;color:#fff;font-size:12px;line-height:14px;text-align:center;font-weight:700}

/* features */
.feature{top:440px;width:180px;text-align:center}
.feature svg{display:block;margin:0 auto}
.feature h3{font-size:9.5px;font-weight:700;margin-top:10px}
.feature h3.hl{color:var(--blue)}
.feature p{font-size:7px;line-height:10px;color:var(--muted);margin-top:5px}

/* services */
.services{top:610px;left:0;width:672px;height:178px;background:var(--pale)}
.section-title{width:672px;text-align:center;font-size:17px;font-weight:400;color:var(--ink)}
.section-title span{color:var(--blue)}
.title-rule{left:250px;width:172px;height:1px;background:#bbb}
.title-mark{left:331px;width:9px;height:9px;background:var(--blue-dark)}
.card{top:60px;width:165px;height:94px}
.card-photo{width:100%;height:100%}
.card-caption{bottom:0;left:0;width:100%;height:19px;background:rgba(11,79,138,.85);color:#fff;font-size:10px;text-align:center;line-height:19px}
.card-panel{background:linear-gradient(#1d5a9a,#0c4a88);color:#fff;text-align:center;padding-top:14px}
.card-panel h4{font-size:10px;font-weight:700}
.card-panel p{font-size:6.3px;line-height:10px;width:140px;margin:5px auto 0}
.card-panel .more{font-size:6.3px;font-weight:700;margin-top:4px}
.chev{top:64px}

/* testimonial */
.portrait{left:70px;top:858px;width:80px;height:80px;border-radius:50%;border:3px solid #ccc;background:linear-gradient(#c8ccd0,#55606c)}
.quote{left:166px;top:854px;width:445px;font-size:7px;line-height:14px;font-style:italic;color:#555;text-align:center}
.quote-rule{left:166px;top:918px;width:445px;height:1px;background:#ddd}
.author{left:222px;top:928px;font-size:7px;font-weight:700;color:var(--blue-dark)}
.dots{left:523px;top:929px;display:flex;gap:3px}
.dots i{width:5px;height:5px;border-radius:50%;background:#ccc}
.dots i:first-child{background:var(--blue)}

/* footer */
.wave{top:920px;left:0}
.footer{top:1004px;left:0;width:672px;height:170px;background:var(--navy)}
.footer h5{font-size:9.5px;font-weight:600;color:#fff}
.col{top:30px}
.links li{list-style:none;font-size:6.5px;color:#fff;margin-top:13px;padding-left:6px;position:relative}
.links li::before{content:"";position:absolute;left:0;top:3px;width:2px;height:2px;background:#fff}
.info-row{display:flex;gap:7px;font-size:6.5px;line-height:9px;color:#fff;margin-top:10px}
.info-row svg{flex:none;margin-top:1px}
.divider{top:26px;width:1px;height:130px;background:rgba(0,0,0,.18)}
.field{width:151px;height:19px;border:1px solid rgba(255,255,255,.55);font-size:6.5px;color:#fff;padding:5px 7px;margin-top:4px}
.field.msg{height:34px}
.submit{width:58px;height:18px;background:linear-gradient(#fff,#ddd);color:#333;font-size:7.5px;text-align:center;line-height:18px;margin-top:9px;border-radius:2px}
.foot-brand{left:500px;top:64px;display:flex;align-items:center;gap:6px}
.foot-brand .brand-square{background:#fff}
.foot-brand .brand-name{color:#fff;font-size:12px}
.social{left:504px;top:110px;display:flex;gap:8px}
.social i{width:17px;height:17px;display:block}
.copyright{top:1174px;left:0;width:672px;height:26px;background:var(--navy-deep);color:#cfe0f0;font-size:7px;text-align:center;line-height:26px}
</style>
</head>
<body>

<header class="abs header">
  <div class="abs brand"><span class="brand-square"></span><span class="brand-name">Beacon Advisory</span></div>
  <div class="abs contact-chip" style="left:375px">
    <span class="chip-dot"></span>
    <div><div class="chip-label">CALL US</div><div class="chip-value">+1 (555) 014 2290</div></div>
  </div>
  <div class="abs contact-chip" style="left:476px">
    <span class="chip-dot"></span>
    <div><div class="chip-label">EMAIL US</div><div class="chip-value">info@beaconadvisoryinc.com</div></div>
  </div>
</header>

<nav class="abs nav">
  <a class="active" href="#" style="width:62px">HOME</a>
  <a href="#" style="width:84px">ABOUT US</a>
  <a href="#" style="width:78px">SERVICES</a>
  <a href="#" style="width:84px">SOLUTIONS</a>
  <a href="#" style="width:86px">RESOURCES</a>
  <a href="#" style="width:71px">CAREER</a>
  <a href="#" style="width:88px;border:0">CONTACT US</a>
</nav>

<section class="abs hero" role="img" aria-label="Photo of two businessmen looking at a screen together">
  <h2 class="abs hero-title">DELIVERS HIGHEST LEVEL OF QUALITY CONSULTANTS AND SERVICES FOR THE LOWEST COST OF OWNERSHIP</h2>
  <div class="abs btn">READ MORE</div>
</section>

<section class="abs welcome">
  <h1>Welcome To Beacon Advisory Inc</h1>
  <div class="rule"></div>
  <p>Today's IT market is a dynamic, fast-paced industry, with ever-increasing demands. Meeting these demands for over 25 years, Beacon Advisory maintains a global presence, aggressively recruiting expertly qualified IT and Management Professionals from around the world and cultivating key partnerships with corporations to understand their business models end-to-end, with a goal of delivering exceptional client service and ensuring a consistent delivery....</p>
</section>
<div class="abs plus">+</div>

<div class="abs feature" style="left:60px">
  <svg width="90" height="90" viewBox="0 0 90 90" fill="none" stroke="#444" stroke-width="1">
    <path d="M37 8l8-8 8 8M37 82l8 8 8-8M8 37l-8 8 8 8M82 37l8 8-8 8" transform="translate(0,0)"/>
    <g fill="#222" stroke="none"><circle cx="37" cy="37" r="3"/><circle cx="53" cy="37" r="3"/><rect x="33" y="41" width="8" height="9"/><rect x="49" y="41" width="8" height="9"/><rect x="34" y="46" width="22" height="3"/><rect x="40" y="50" width="10" height="4"/></g>
  </svg>
  <h3>CONSULTING</h3>
  <p>Beacon Advisory has certified professional consultants to work with you to help increase the business by providing IT services ...</p>
</div>

<div class="abs feature" style="left:246px">
  <svg width="90" height="90" viewBox="0 0 90 90" fill="none" stroke="#1aa0de" stroke-width="1">
    <path d="M37 2l8 8 8-8M37 88l8-8 8 8M10 37l8 8-8 8M80 37l-8 8 8 8"/>
    <circle cx="45" cy="45" r="8" stroke-width="6" stroke-dasharray="3.2 2.2"/>
    <circle cx="45" cy="45" r="5" fill="#1aa0de" stroke="none"/>
    <circle cx="45" cy="45" r="2.2" fill="#fff" stroke="none"/>
  </svg>
  <h3 class="hl">STAFF AUGMENTATION</h3>
  <p>For years Beacon Advisory as been offering our customers the ability to augment their existing staff..</p>
</div>

<div class="abs feature" style="left:437px">
  <svg width="90" height="90" viewBox="0 0 90 90" fill="none" stroke="#444" stroke-width="1">
    <path d="M37 8l8-8 8 8M37 82l8 8 8-8M8 37l-8 8 8 8M82 37l8 8-8 8"/>
    <rect x="33" y="33" width="24" height="24" rx="4" fill="#222" stroke="none"/>
  </svg>
  <h3>OFFSHORE</h3>
  <p>Our Offshore development model has a unique distinction of providing efficient software solutions ...</p>
</div>

<section class="abs services">
  <h2 class="abs section-title" style="top:10px">Our <span>Services</span></h2>
  <div class="abs title-rule" style="top:36px"></div>
  <div class="abs title-mark" style="top:32px"></div>
  <svg class="abs chev" style="left:28px" width="16" height="30"><path d="M15 1L1 15l14 14" fill="none" stroke="#888"/></svg>
  <svg class="abs chev" style="left:626px" width="16" height="30"><path d="M1 1l14 14L1 29" fill="none" stroke="#888"/></svg>
  <div class="abs card" style="left:60px">
    <div class="card-photo" role="img" aria-label="Photo of a hand touching a glowing network of technology icons" style="background:radial-gradient(circle at 45% 40%,#3a6f9a,#0d1f33 75%)"></div>
    <div class="abs card-caption">Technology</div>
  </div>
  <div class="abs card card-panel" style="left:253px">
    <h4>OFFSHORE</h4>
    <p>Our Offshore development model has a unique distinction of providing efficient software solutions with cost and quality advantage, using state-of-the-art</p>
    <div class="more">READ MORE »</div>
  </div>
  <div class="abs card" style="left:447px">
    <div class="card-photo" role="img" aria-label="Photo of a man touching floating application icons" style="background:linear-gradient(120deg,#7fc4e8,#1d5f93 60%,#0e2d4e)"></div>
    <div class="abs card-caption">Application Developement</div>
  </div>
</section>

<h2 class="abs section-title" style="top:806px">Client <span>Testimonial</span></h2>
<div class="abs title-rule" style="top:834px"></div>
<div class="abs title-mark" style="top:830px"></div>
<div class="abs portrait" role="img" aria-label="Portrait photo of the client"></div>
<p class="abs quote">“ Lorem ipsum dolor sit amet, consectetuer adipiscing elit, sed diam nonummy nibh euismod tincidunt utvm laoreetm dolore magna aliquam erat volutpat. Ut wisi enim ad minim veniam, quis nostrud exerci tation ullamcorper suscipit lobortis nisl utmv aliquip ex ea commodo consequat. Duis autem vel eum iriure dolor in hendrerit in vulputate velit esse molestie consequat, velm illu dolore eu feugiat nulla facilisis at vero eros et accumsan etsto duis facilisi. ”</p>
<div class="abs quote-rule"></div>
<div class="abs author">- Miss Clara Hollis</div>
<div class="abs dots"><i></i><i></i><i></i><i></i></div>

<svg class="abs wave" width="672" height="90" viewBox="0 0 672 90">
  <path d="M0 84 C90 40 170 40 300 60 C430 80 560 60 672 14 L672 90 L0 90Z" fill="#1a5ea6"/>
  <path d="M270 60 C420 90 570 70 672 12 L672 22 C570 80 420 96 270 60Z" fill="#12a8ea"/>
</svg>

<footer class="abs footer">
  <div class="abs col" style="left:59px">
    <h5>Quick Links</h5>
    <ul class="links"><li>Home</li><li>About Us</li><li>Services</li><li>Resources</li><li>Contact Us</li></ul>
  </div>
  <div class="abs divider" style="left:133px"></div>
  <div class="abs col" style="left:159px;width:130px">
    <h5>Contact Information</h5>
    <div class="info-row"><svg width="7" height="9"><path d="M3.5 0a3.5 3.5 0 0 1 3.5 3.5C7 6 3.5 9 3.5 9S0 6 0 3.5A3.5 3.5 0 0 1 3.5 0z" fill="#fff"/></svg><span>418 Harbor Lane<br>Suite 12<br>Westfield, NJ 07090</span></div>
    <div class="info-row" style="margin-top:14px"><svg width="7" height="7"><path d="M1 0h2l1 2-1 1c.5 1 1 1.5 2 2l1-1 2 1v2C3 7 0 4 1 0z" fill="#fff"/></svg><span>+1 (555) 014 2290</span></div>
    <div class="info-row" style="margin-top:14px"><svg width="8" height="7"><rect x="0" y="2" width="8" height="4" fill="#fff"/><rect x="2" y="0" width="4" height="2" fill="#fff"/></svg><span>555.010.4417</span></div>
    <div class="info-row" style="margin-top:14px"><svg width="8" height="6"><rect width="8" height="6" fill="#fff"/><path d="M0 0l4 3 4-3" stroke="#1a5ea6" fill="none"/></svg><span>hello@beaconmail.com</span></div>
  </div>
  <div class="abs divider" style="left:280px"></div>
  <div class="abs col" style="left:306px">
    <h5>Quick Contact</h5>
    <div class="field" style="margin-top:9px">Name</div>
    <div class="field">Phone</div>
    <div class="field msg">Message</div>
    <div class="submit">SUBMIT</div>
  </div>
  <div class="abs divider" style="left:474px"></div>
  <div class="abs foot-brand"><span class="brand-square"></span><span class="brand-name">Beacon Advisory</span></div>
  <div class="abs social">
    <i style="background:#2a4f8f"></i><i style="background:#3fa3d8"></i><i style="background:#1878b8"></i><i style="background:#f39a1e"></i>
  </div>
</footer>

<div class="abs copyright">Copyright © 2016 Beaconadvisoryinc. All Rights Reserved.</div>

</body>
</html>
```